We need a new business card that reflects who we are. Professional, classy, modern, and service ori

We need a business card design for a window coverings design company in Kansas City called Bright Lane Interiors. We offer professional, modern, and high quality window covering products. We are looking to portray an image of a big, national franchise. We are a 5 location (with showrooms) business with 10 professional designers and 4 professional installers. These cards will be used with Thank you cards, given to realtors, and asked for referrals with.

Target Market(s)

Kansas City

Industry/Entity Type

Business

Contact Information for Business Card

We would like our card to look clean and simple on the front, featuring our logo and Marlow Fenwick's. Our designers' phone numbers and emails should be displayed as well as their title.

Font styles to use
Sans Serif

Colors

Designer to choose colors to be used in the design.

Requirements
Must have
• Front - Logos, name, phone number, email address
• Back - Showroom locations, social media? Appt date/time?
Nice to have
• I would like a clean and modern look (not contemporary. I like a white background, but I am open to ideas. Looking for a "National chain" look for a small business.
Should not have
• Too much busyness.

```html
<!DOCTYPE html>
<html lang="en">
<head>
<meta charset="utf-8">
<title>Bright Lane Interiors — Business Card</title>
<link rel="stylesheet" href="https://fonts.googleapis.com/css2?family=Tinos:wght@400;700&family=Roboto+Condensed:wght@400;700&family=Roboto:wght@400&display=swap">
<style>
  :root {
    --backdrop: #2b2b2b;
    --card: #f3f3f3;
    --ink: #1c1c1c;
    --text-grey: #4a4a4a;
    --partner-grey: #5d6670;
    --brand-red: #c9434a;
    --band-grey: #8e9094;
    --dots: #9a9a9a;
  }
  * { margin: 0; padding: 0; box-sizing: border-box; }
  html, body { width: 1200px; height: 960px; overflow: hidden; }
  body { background: var(--backdrop); position: relative; }

  .card {
    position: absolute;
    width: 600px;
    height: 343px;
    background: var(--card);
    box-shadow: 0 3px 10px rgba(0,0,0,0.55);
    overflow: hidden;
  }
  .card--front { left: 314px; top: 113px; font-family: "Tinos", "Times New Roman", serif; }
  .card--back  { left: 311px; top: 472px; font-family: "Roboto Condensed", "Arial Narrow", sans-serif; }

  /* Front */
  .brand {
    position: absolute; left: 0; right: 0; top: 112px;
    display: flex; align-items: center; justify-content: center; gap: 12px;
  }
  .brand__mark { width: 22px; height: 22px; background: var(--brand-red); }
  .brand__name { font-size: 32px; color: var(--ink); font-weight: 400; letter-spacing: 0.5px; }
  .tagline {
    position: absolute; left: 0; right: 0; top: 167px;
    text-align: center; font-size: 14px; color: var(--ink);
  }
  .designer {
    position: absolute; left: 0; right: 0; top: 228px;
    text-align: center; font-size: 15px; color: var(--ink); letter-spacing: 0.5px;
  }
  .designer__name { color: var(--brand-red); font-weight: 700; font-size: 22px; letter-spacing: 0; }
  .designer__dash { color: var(--brand-red); font-weight: 700; margin: 0 10px 0 6px; }
  .contact {
    position: absolute; left: 0; right: 0; top: 259px;
    text-align: center; font-size: 15px; color: var(--text-grey);
  }
  .contact__label { color: var(--brand-red); font-weight: 700; }
  .band { position: absolute; left: 0; right: 0; bottom: 0; height: 13px; background: var(--band-grey); }
  .web {
    position: absolute; left: 146px; bottom: 0; width: 308px; height: 37px;
    background: var(--brand-red); color: #1a1a1a;
    display: flex; align-items: center; justify-content: center;
    font-size: 14px; letter-spacing: 2.2px;
  }

  /* Back */
  .partner {
    position: absolute; left: 0; right: 0; top: 40px;
    text-align: center;
    font-size: 16px; font-weight: 400; color: var(--partner-grey);
  }
  .appointments { position: absolute; left: 82px; top: 82px; width: 440px; }
  .appt {
    display: flex; align-items: baseline; height: 45.5px;
    font-family: "Roboto", Arial, sans-serif; color: var(--brand-red);
  }
  .appt__label { font-size: 16px; }
  .appt__line { border-bottom: 1px dotted var(--dots); margin: 0 2px 0 5px; transform: translateY(-3px); }
  .appt__line--date { width: 168px; }
  .appt__line--time { width: 106px; }
  .appt__ampm { font-size: 12px; margin-left: 3px; }
  .showrooms { position: absolute; left: 0; right: 0; top: 260px; text-align: center; }
  .showrooms__title { color: var(--brand-red); font-weight: 700; font-size: 15px; }
  .showrooms__list { color: var(--text-grey); font-size: 13.5px; margin-top: 3px; }
  .social { position: absolute; left: 0; right: 0; top: 302px; display: flex; justify-content: center; gap: 3px; }
  .social__dot { width: 20px; height: 20px; border-radius: 50%; background: var(--brand-red); }
</style>
</head>
<body>

<section class="card card--front" aria-label="Card front">
  <div class="brand">
    <span class="brand__mark"></span>
    <span class="brand__name">Bright Lane Interiors</span>
  </div>
  <p class="tagline">Blinds, Shades, Shutters, Draperies &amp; Decor</p>
  <p class="designer"><span class="designer__name">DANIEL REYES</span><span class="designer__dash">-</span>DESIGNER</p>
  <p class="contact"><span class="contact__label">Phone:</span> 913.555.0148 <span class="contact__label">Email:</span> info@brightlaneinteriors.com</p>
  <div class="band"></div>
  <div class="web">www.brightlaneinteriors.com</div>
</section>

<section class="card card--back" aria-label="Card back">
  <p class="partner">Marlow Fenwick</p>
  <div class="appointments">
    <div class="appt"><span class="appt__label">Date :</span><span class="appt__line appt__line--date"></span><span class="appt__label">Time :</span><span class="appt__line appt__line--time"></span><span class="appt__ampm">AM/PM</span></div>
    <div class="appt"><span class="appt__label">Date :</span><span class="appt__line appt__line--date"></span><span class="appt__label">Time :</span><span class="appt__line appt__line--time"></span><span class="appt__ampm">AM/PM</span></div>
    <div class="appt"><span class="appt__label">Date :</span><span class="appt__line appt__line--date"></span><span class="appt__label">Time :</span><span class="appt__line appt__line--time"></span><span class="appt__ampm">AM/PM</span></div>
    <div class="appt"><span class="appt__label">Date :</span><span class="appt__line appt__line--date"></span><span class="appt__label">Time :</span><span class="appt__line appt__line--time"></span><span class="appt__ampm">AM/PM</span></div>
  </div>
  <div class="showrooms">
    <p class="showrooms__title">SHOWROOM LOCATIONS</p>
    <p class="showrooms__list">RIVERSIDE | OAK HILL PARK | CEDAR POINT | NORTHGATE | MAPLE GROVE</p>
  </div>
  <div class="social" aria-label="Social media">
    <span class="social__dot"></span>
    <span class="social__dot"></span>
    <span class="social__dot"></span>
    <span class="social__dot"></span>
  </div>
</section>

</body>
</html>
```